Please wait to be seated sign A1

We need a sign for our guests on arrival before they get seated:
A1 Size with a 2.2mm bleed
(text)
please wait - someone from our flock will be with you soon.
(must have)
Pink, Simple, Bright and Fun
We are The Velvet Heron and we put on shows so we need it to be creative. Show venue so the use of curtains or stage shows and lots of pink needs to be used. Logo centre up the the top.
Sign 2: Toilet Sign
We want something cute for a toilet directional sign
Female Flamingo and Male Flamingo
(text)
Toilets this way - if there is a cute saying or something cheeky we can do this also
Sign 3:
Platinum Members Only
Sign 4:
Gold Members Only
Sign 5:
Powder Room
Sign 6:
Arrow Sign - See photo for reference
50cm x 18cm with a 2.2mm bleed
Box Office
Sign 7:
Riverside Entry
velvetheronshows.example is the website for reference to who we are fonts and posters we use for our shows. Keep to all pink and cute.
Target Market(s)
20 - 55
Industry/Entity Type
Entertainment
Look and feel
Each slider illustrates characteristics of the customer's brand and the style your logo design should communicate.

```html
<!DOCTYPE html>
<html lang="en">
<head>
<meta charset="utf-8">
<title>Please Wait Sign – The Velvet Heron</title>
<link rel="stylesheet" href="https://fonts.googleapis.com/css2?family=Montserrat:wght@700&family=Poiret+One&display=swap">
<style>
  :root {
    --backdrop: #1d1d1d;
    --card: #ffffff;
    --pink: #e91fae;
    --curtain: #d8239f;
    --mark: #111111;
  }
  * { margin: 0; padding: 0; box-sizing: border-box; }
  html, body {
    width: 1200px;
    height: 900px;
    overflow: hidden;
    background: var(--backdrop);
  }
  .canvas {
    width: 1200px;
    height: 900px;
    display: flex;
    align-items: center;
    justify-content: center;
  }
  .sign {
    position: relative;
    width: 608px;
    height: 860px;
    background: var(--card);
    overflow: hidden;
  }
  .stage-curtains {
    position: absolute;
    top: 0;
    left: 0;
    width: 608px;
    height: 600px;
  }
  .brand {
    position: absolute;
    top: 276px;
    left: 0;
    right: 0;
    display: flex;
    align-items: center;
    justify-content: center;
    gap: 10px;
  }
  .brand-dot {
    width: 22px;
    height: 22px;
    border-radius: 50%;
    background: var(--mark);
  }
  .brand-name {
    font-family: "Montserrat", sans-serif;
    font-weight: 700;
    font-size: 22px;
    color: var(--pink);
  }
  .headline {
    font-family: "Poiret One", sans-serif;
    font-weight: 400;
    color: var(--pink);
    -webkit-text-stroke: 1.6px var(--pink);
  }
  .headline span {
    position: absolute;
    left: 0;
    right: 0;
    text-align: center;
    line-height: 1;
  }
  .headline-please { top: 440px; font-size: 92px; letter-spacing: 9px; padding-left: 9px; }
  .headline-wait { top: 518px; font-size: 128px; letter-spacing: 6px; padding-left: 6px; }
  .subline {
    position: absolute;
    top: 640px;
    left: 0;
    right: 0;
    text-align: center;
    font-family: "Montserrat", sans-serif;
    font-weight: 700;
    font-size: 30px;
    line-height: 1.28;
    letter-spacing: 0.5px;
    color: var(--pink);
  }
</style>
</head>
<body>
  <main class="canvas">
    <section class="sign">
      <svg class="stage-curtains" viewBox="0 0 608 600" role="img" aria-label="Illustration: pink theatre stage curtains with tasselled valance framing the top and sides of the sign">
        <path fill="var(--curtain)" d="M0 0 H608 V590 H550 V100 H58 V590 H0 Z"/>
      </svg>

      <div class="brand">
        <span class="brand-dot"></span>
        <span class="brand-name">The Velvet Heron</span>
      </div>

      <h1 class="headline">
        <span class="headline-please">PLEASE</span>
        <span class="headline-wait">WAIT</span>
      </h1>
      <p class="subline">SOMEONE FROM<br>OUR FLOCK WILL<br>BE WITH YOU SOON.</p>
    </section>
  </main>
</body>
</html>
```